Homeowners Insurance Provider Website

We are selling homeowners insurance policy / tenants Policy/Flood Insurance in USA in few states and planning expand nationally.

Our target audience are two folds: Customers (Buy policies) and Insurance Agents who wants to work with us to sell our policies to customers. But website should focus 80% on customers and 20% on agents. So, more customer focused user experience. Please note that there is no direct buy option for customers. They always go through insurance agents.

Customer focused, educational that makes buyer journey easy. We don’t want to come off as trying sell something as there is no direct sales involved from website.

Target Market(s)

Homeowners in USA and Insurance agent who sells these insurance.

Industry/Entity Type

Insurance

Number of Pages Required

4 page

Font styles to use
Other font styles liked:
• Open to suggestions

Colors

Designer to choose colors to be used in the design.

Requirements
Must have
• Three most important things: Trustworthy, Authentic, Simple
• Please use colors form logo and grays
• We like: www.hollowmere.com
• https://www.quillfenbrook.com/
• We need Agent Look up tool on home page similar to what is shown on example sites.
• Design:
• Home Page - Open to Ideas
• Insurance (Products) Landing Page - Info similar to: https://www.quillfenbrook.com/insurance/
• Agents Page - https://www.quillfenbrook.com/agents/
• Claims Page - Information similar to: https://www.quillfenbrook.com/claims-center/
• Site Navigation:
• Home
• Insurance
• Claims
• Agents
• About Us
• Contact Us
Nice to have
• Elegant, minimal and clean design that reflects trust and authenticity.
Should not have
• Slider or rotating images - prefer flat design. Not over powering design.

```html
<!DOCTYPE html>
<html lang="en">
<head>
<meta charset="utf-8">
<title>Hearthline Insurance Co. — Home</title>
<link href="https://fonts.googleapis.com/css2?family=Lato:wght@300;400;700;900&family=Open+Sans:wght@400;600;700&display=swap" rel="stylesheet">
<style>
:root{
  --navy:#1f3b7c;
  --navy-deep:#1a3170;
  --red:#d3222f;
  --ink:#2b2b2b;
  --body:#4a4a4a;
  --grey-bg:#f5f5f5;
  --line:#d9d9d9;
  --white:#ffffff;
}
*{margin:0;padding:0;box-sizing:border-box}
html,body{width:1200px;height:3455px;overflow:hidden;background:var(--white)}
body{font-family:"Open Sans",Arial,sans-serif;color:var(--body);position:relative}
.page{position:relative;width:1200px;height:3455px;overflow:hidden}
section,header,footer{position:absolute;left:0;width:1200px}
.abs{position:absolute}
h2{font-family:"Lato",Arial,sans-serif;font-weight:400;font-size:26px;letter-spacing:1px;color:var(--navy);text-transform:uppercase;white-space:nowrap}
h2 b{font-weight:900}
.divider{display:block;height:12px;position:relative}
.divider::before{content:"";position:absolute;top:5px;left:0;right:0;height:1px;background:var(--line)}
.divider::after{content:"";position:absolute;top:1px;left:0;width:9px;height:9px;border-radius:50%;background:#bdbdbd}
.divider.center::after{left:50%;margin-left:-4px}
p.copy{font-size:13px;line-height:22px;color:var(--body)}
.btn{position:absolute;display:flex;align-items:center;height:36px;background:var(--red);color:var(--white);font-family:"Lato",Arial,sans-serif;font-weight:700;font-size:15px;padding:0 22px;text-decoration:none;white-space:nowrap}

/* header */
.site-header{top:0;height:101px;background:rgba(255,255,255,.93);z-index:5}
.brand{left:113px;top:16px;display:flex;align-items:center;gap:14px}
.brand .mark{width:44px;height:44px;background:var(--navy)}
.brand .name{font-family:"Lato",Arial,sans-serif;font-weight:700;font-size:26px;line-height:27px;color:var(--navy);letter-spacing:.5px}
.brand .name small{display:block;font-size:18px;letter-spacing:3px}
.topbar{right:103px;top:0;height:28px;display:flex}
.topbar .phone{background:var(--navy);color:var(--white);font-family:"Lato",sans-serif;font-weight:700;font-size:16px;padding:0 24px 0 34px;display:flex;align-items:center;gap:10px;clip-path:polygon(14px 0,100% 0,100% 100%,0 100%)}
.topbar .consult{background:var(--red);color:var(--white);font-family:"Lato",sans-serif;font-weight:700;font-size:13px;padding:0 22px 0 14px;display:flex;align-items:center;clip-path:polygon(0 0,100% 0,calc(100% - 12px) 100%,0 100%)}
.nav{right:105px;top:64px;display:flex;align-items:center;font-family:"Lato",sans-serif;font-weight:700;font-size:13px;letter-spacing:.8px;color:var(--ink)}
.nav a{color:var(--ink);text-decoration:none;padding:0 20px;border-left:1px solid var(--line);line-height:14px}
.nav .home{border:none;padding:0 20px 0 0}

/* hero */
.hero{top:0;height:622px;background:linear-gradient(180deg,#c7c5c2 0%,#8e8b88 45%,#5b5855 100%)}
.hero-headline{top:408px;left:0;width:1200px;text-align:center;font-family:"Lato",sans-serif;font-weight:300;font-size:26px;line-height:37px;letter-spacing:1.5px;color:var(--white);text-transform:uppercase}
.hero-headline b{font-weight:900}
.hero .btn{left:508px;top:546px}

/* welcome */
.welcome{top:622px;height:418px;background:var(--grey-bg)}
.welcome h2{left:113px;top:76px}
.welcome .divider{left:113px;top:120px;width:610px}
.welcome p{left:113px;top:155px;width:624px}
.welcome .btn{left:113px;top:308px}
.welcome .photo{left:772px;top:120px;width:315px;height:221px;border:2px solid var(--navy);background:linear-gradient(160deg,#7d8f9c,#c9a48c 55%,#8a5b4c)}

/* services */
.services{top:1040px;height:490px;background:var(--white)}
.services h2{left:0;width:1200px;text-align:center;top:70px}
.services .divider{left:398px;width:404px;top:117px}
.card{position:absolute;top:168px;width:316px;height:248px;text-align:center}
.card svg.frame{position:absolute;left:0;top:0}
.card .icon{position:absolute;left:136px;top:28px;width:44px;height:50px;border-radius:4px;background:var(--navy)}
.card h3{position:absolute;left:0;width:100%;top:92px;font-family:"Lato",sans-serif;font-weight:900;font-size:15px;color:var(--ink);letter-spacing:.5px}
.card p{position:absolute;left:28px;width:260px;top:120px;font-size:12px;line-height:18px;color:var(--body)}
.card .more{position:absolute;left:0;width:100%;top:203px;font-family:"Lato",sans-serif;font-weight:900;font-size:12px;color:var(--navy);text-decoration:underline}
.card .more.red{color:var(--red)}

/* agents */
.agents{top:1530px;height:377px;background:#f3f3f3}
.agents .photo{left:0;top:0;width:610px;height:377px;background:linear-gradient(90deg,#6f7478 0%,#c8c1b8 45%,#e6e1dc 80%,rgba(243,243,243,0) 100%)}
.agents h2{left:585px;top:68px}
.agents .divider{left:585px;top:112px;width:502px}
.agents p{left:590px;top:150px;width:500px;font-size:13px;line-height:22px}
.agents .btn{left:592px;top:266px}

/* claims */
.claims{top:1907px;height:746px;background:var(--white)}
.claims .photo{left:580px;top:0;width:620px;height:746px;background:linear-gradient(90deg,rgba(255,255,255,1) 0%,rgba(220,210,200,.6) 18%,#b49a87 45%,#8b6f62 75%,#6d6763 100%)}
.claims h2{left:113px;top:70px}
.claims .divider{left:113px;top:112px;width:345px}
.claims p.lead{left:113px;top:150px;width:600px;font-size:13px;line-height:22px}
.claim-box{position:absolute;left:113px;width:465px;height:174px;border:1px solid var(--line);background:rgba(255,255,255,.96)}
.claim-box::before{content:"";position:absolute;left:0;top:0;width:24px;height:2px;background:var(--navy)}
.claim-box h3{position:absolute;left:26px;top:24px;font-family:"Lato",sans-serif;font-weight:700;font-size:17px;color:var(--ink)}
.claim-box p{position:absolute;left:26px;top:56px;width:420px;font-size:13px;line-height:22px;color:var(--body)}
.claim-box .btn{left:26px;top:112px;height:34px}

/* testimonials */
.testimonials{top:2653px;height:420px;background:var(--white)}
.testimonials h2{left:0;width:1200px;text-align:center;top:65px}
.testimonials .divider{left:400px;width:400px;top:110px}
.testimonials .photo{left:113px;top:168px;width:244px;height:189px;background:linear-gradient(160deg,#5d7b53,#a8a08e 55%,#6e5a4a)}
.testimonials .quote-tag{left:345px;top:244px;width:52px;height:52px;background:var(--red);display:flex;align-items:center;justify-content:center}
.testimonials .qmark{left:421px;top:162px;font-family:Georgia,serif;font-size:56px;color:#d6d6d6;line-height:1}
.testimonials p{left:460px;top:166px;width:627px;font-size:13px;line-height:23px}
.testimonials .who{left:421px;top:336px;font-family:"Lato",sans-serif;font-weight:900;font-size:14px;color:var(--navy)}
.testimonials .rule{left:421px;top:325px;width:666px;height:1px;background:var(--line)}
.dots{left:1053px;top:349px;display:flex;gap:5px}
.dots i{width:8px;height:8px;border-radius:50%;background:#c9c9c9}
.dots i:first-child{background:#9a9a9a}

/* footer */
.footer-band{top:3136px;left:0;width:1200px;height:14px;background:var(--red)}
.site-footer{top:3150px;height:265px;background:var(--navy-deep);color:var(--white)}
.site-footer h4{font-family:"Lato",sans-serif;font-weight:900;font-size:14px;color:var(--white)}
.col-links{left:113px;top:60px}
.col-links ul{list-style:none;margin-top:14px}
.col-links li{font-size:12px;line-height:21px;color:#dfe5f3;padding-left:14px;position:relative}
.col-links li::before{content:"›";position:absolute;left:0;color:var(--red);font-weight:700}
.col-links .underline{width:92px;height:1px;background:#4d62a0;margin-top:8px}
.col-contact{left:302px;top:60px;width:270px}
.col-contact .row{display:flex;gap:12px;margin-top:18px;font-size:12px;line-height:17px;color:#dfe5f3}
.col-contact .row:first-of-type{margin-top:24px}
.col-contact svg{flex:none;margin-top:2px}
.col-map{left:594px;top:60px}
.col-map .map{margin-top:24px;width:190px;height:116px;background:linear-gradient(135deg,#dfe7d8,#c9d6e4 60%,#e8e3d6);border:3px solid var(--white)}
.foot-brand{left:864px;top:105px;display:flex;align-items:center;gap:12px}
.foot-brand .mark{width:40px;height:40px;border:2px solid var(--white)}
.foot-brand .name{font-family:"Lato",sans-serif;font-weight:700;font-size:22px;line-height:22px;color:var(--white)}
.foot-brand .name small{display:block;font-size:15px;letter-spacing:2.5px}
.socials{left:925px;top:175px;display:flex;gap:14px}
.socials i{width:30px;height:30px;border-radius:50%;border:1.5px solid var(--white);display:block}
.vsep{top:60px;width:1px;height:165px;background:#3a5093}
.copyright{top:3415px;height:40px;background:var(--red);color:var(--white);text-align:center;font-family:"Lato",sans-serif;font-weight:700;font-size:12px;line-height:40px}
</style>
</head>
<body>
<div class="page">

  <section class="hero" role="img" aria-label="Photo of a team of colleagues in discussion around a meeting table">
    <h1 class="abs hero-headline">We are selling homeowners <b>insurance policy,tenants<br>policy,flood insurance</b> in USA in few states and<br>planning to expand nationally</h1>
    <a class="btn" href="#">Call Us Today</a>
  </section>

  <header class="site-header">
    <div class="abs brand"><span class="mark"></span><span class="name">HEARTHLINE<small>INSURANCE CO.</small></span></div>
    <div class="abs topbar">
      <span class="phone"><svg width="16" height="16" viewBox="0 0 24 24"><circle cx="12" cy="12" r="11" fill="none" stroke="#fff" stroke-width="2"/><path d="M8 6l2 3-1.5 1.5a8 8 0 0 0 5 5L15 14l3 2-1 2.5c-5 0-10-5-10-10z" fill="#fff"/></svg>555 010 2400</span>
      <span class="consult">Get A Free Consultation</span>
    </div>
    <nav class="abs nav">
      <a class="home" href="#"><svg width="20" height="18" viewBox="0 0 20 18"><path d="M10 1L1 9h3v8h4v-5h4v5h4V9h3z" fill="#d3222f"/></svg></a>
      <a href="#">ABOUT US</a><a href="#">INSURANCE</a><a href="#">CLAIMS</a><a href="#">AGENTS</a><a href="#">CONTACT US</a>
    </nav>
  </header>

  <section class="welcome">
    <h2 class="abs"><b>Welcome to Hearthline</b> Insurance Co.</h2>
    <span class="abs divider"></span>
    <p class="abs copy">Lorem ipsum dolor sit amet, consectetuer adipiscing elit, sed diam nonummy nibh euismod tincidunt ut laoreetfgf dolore magna aliquam erat volutpat. tincidunt ut laoreetfgf dolore magna aliquam erat volutpat. Lorem ipsum dolor sit amet, consectetuer adipiscing elit, sed diam nonummy nibh euismod tincidunt.volutpat. Lorem ipsum dolor sit amet, consectetuer adipiscing elit, sed diam nonummy nibh euismod tincidunt.</p>
    <a class="btn" href="#">Read More</a>
    <div class="abs photo" role="img" aria-label="Photo of a smiling family in front of their house"></div>
  </section>

  <section class="services">
    <h2 class="abs"><b>Our</b> Services</h2>
    <span class="abs divider center"></span>
    <div class="card" style="left:113px">
      <svg class="frame" width="316" height="248"><polygon points="0.5,12 158,0.5 315.5,12 315.5,247.5 0.5,247.5" fill="#fff" stroke="#d9d9d9"/></svg>
      <span class="icon"></span><h3>FLOOD INSURANCE</h3>
      <p>Lorem ipsum dolor sit amet, consectetuer pmbe adipiscing elit, sed diam nonummy nibh euistincidunt ut laoreetfgf</p>
      <a class="more red" href="#">MORE</a>
    </div>
    <div class="card" style="left:442px">
      <svg class="frame" width="316" height="248"><polygon points="0.5,12 158,0.5 315.5,12 315.5,247.5 0.5,247.5" fill="#fff" stroke="#d9d9d9"/></svg>
      <span class="icon"></span><h3>INSURANCE POLICY</h3>
      <p>Lorem ipsum dolor sit amet, consectetuer pmbe adipiscing elit, sed diam nonummy nibh euistincidunt ut laoreetfgf</p>
      <a class="more" href="#">MORE</a>
    </div>
    <div class="card" style="left:771px">
      <svg class="frame" width="316" height="248"><polygon points="0.5,12 158,0.5 315.5,12 315.5,247.5 0.5,247.5" fill="#fff" stroke="#d9d9d9"/></svg>
      <span class="icon"></span><h3>TENANTS POLICY</h3>
      <p>Lorem ipsum dolor sit amet, consectetuer pmbe adipiscing elit, sed diam nonummy nibh euistincidunt ut laoreetfgf</p>
      <a class="more" href="#">MORE</a>
    </div>
  </section>

  <section class="agents">
    <div class="abs photo" role="img" aria-label="Photo of an agent meeting a young couple on a sofa"></div>
    <h2 class="abs"><b>Our Exclusive</b> Agent Programs</h2>
    <span class="abs divider"></span>
    <p class="abs">Lorem ipsum dolor sit amet, consectetuer adipiscing elit, seddiam nonummy nibh euismod tincidunt ut laoreetfgf doloremagna aliquam erat volutpat. tincidunt ut laoreetfgf doloremagna aliquam erat volutpat. Lorem ipsum dolor sit amet, consectetuer adipiscing elit.</p>
    <a class="btn" href="#">Agent Login</a>
  </section>

  <section class="claims">
    <div class="abs photo" role="img" aria-label="Photo of a couple looking at a laptop together"></div>
    <h2 class="abs"><b>Our Claim</b> Process</h2>
    <span class="abs divider"></span>
    <p class="abs lead">Lorem ipsum dolor sit amet, consectetuer adipiscing elit, sed diam nonummy nibh euismo tincidunt ut laoreetfgf dolore magna aliquam erat volutpat. tincidunt ut laoreetfgf doloreu</p>
    <div class="claim-box" style="top:251px">
      <h3>Report a Claim</h3>
      <p>Your safety and security is our number one priority. We aim to make your claim experience as fast and efficient as possible.</p>
      <a class="btn" href="#">Start the Claims Process</a>
    </div>
    <div class="claim-box" style="top:493px">
      <h3>View a Claim</h3>
      <p>Already filed a report and want to track your claim? Login to view your claim status, documents and payment information.</p>
      <a class="btn" href="#">Login to My Policy</a>
    </div>
  </section>

  <section class="testimonials">
    <h2 class="abs"><b>Clients</b> Testimonials</h2>
    <span class="abs divider center"></span>
    <div class="abs photo" role="img" aria-label="Photo of a family sitting together outdoors"></div>
    <div class="abs quote-tag"><svg width="24" height="20" viewBox="0 0 24 20"><path d="M0 20V11C0 5 3 1 9 0v4c-3 1-4 3-4 6h4v10zM14 20V11c0-6 3-10 9-11v4c-3 1-4 3-4 6h4v10z" fill="#fff"/></svg></div>
    <span class="abs qmark">&ldquo;</span>
    <p class="abs">Lorem ipsum dolor smit amet, consectetuer adipiscing elitmk, sed amet diam nonummy nibh euismod tincidun nt ut laoreetml dolore magna aliquam erat volutpat. Ut wisi enim ad minim veniam, quis nostrud exer tationk ullamcorpe suscipit lobortisk nisl utml aliqp ex ea commodo consequat. Duis autem vel eumk iriure dolor inj hendrerit inn vulputate velit esse molestiemo consequat, velhki illumn gnol dolore eu feugiat nulla facilisis . a aliquam erat volutpat. tincidunt ut laoreetfgf dolore unt ut laoreetfgf dolore magna aliquam erat volutpat. tincidunt ut laoreetfgf dolore</p>
    <span class="abs rule"></span>
    <span class="abs who">- Mr. Calder Voss</span>
    <div class="abs dots"><i></i><i></i><i></i></div>
  </section>

  <div class="abs footer-band"></div>

  <footer class="site-footer">
    <div class="abs col-links">
      <h4>Quick Links</h4><div class="underline"></div>
      <ul><li>Home</li><li>About Us</li><li>Insurance</li><li>Claims</li><li>Agents</li><li>Contact Us</li></ul>
    </div>
    <span class="abs vsep" style="left:272px"></span>
    <div class="abs col-contact">
      <h4>Contact Details</h4>
      <div class="row"><svg width="12" height="16" viewBox="0 0 12 16"><path d="M6 0a6 6 0 0 0-6 6c0 4 6 10 6 10s6-6 6-10a6 6 0 0 0-6-6zm0 8.5A2.5 2.5 0 1 1 6 3.5a2.5 2.5 0 0 1 0 5z" fill="#d3222f"/></svg><span>HEARTHLINE INSURANCE CO.<br>123 Maple Ridge Road, Suite 4<br>Springfield</span></div>
      <div class="row"><svg width="13" height="13" viewBox="0 0 24 24"><path d="M5 2l4 5-2 2a12 12 0 0 0 8 8l2-2 5 4-2 3C10 22 2 14 2 4z" fill="#d3222f"/></svg><span>555 - 010 - 2400</span></div>
      <div class="row"><svg width="14" height="11" viewBox="0 0 14 11"><rect width="14" height="11" rx="1" fill="#d3222f"/><path d="M1 1l6 5 6-5" fill="none" stroke="#fff" stroke-width="1.3"/></svg><span>info@hearthlineinsurance.com</span></div>
    </div>
    <span class="abs vsep" style="left:570px"></span>
    <div class="abs col-map">
      <h4>Location Map</h4>
      <div class="map" role="img" aria-label="Street map showing the office location"></div>
    </div>
    <span class="abs vsep" style="left:822px"></span>
    <div class="abs foot-brand"><span class="mark"></span><span class="name">HEARTHLINE<small>INSURANCE CO.</small></span></div>
    <div class="abs socials"><i></i><i></i><i></i></div>
  </footer>

  <div class="abs copyright" style="left:0;width:1200px">Copyright © 2018 Hearthline Insurance Co. All Right Reserved.</div>
</div>
</body>
</html>
```